Business Card Design

Looking for business card designs for a new business. there will be two cards of the same design (both lots of information below in contact info). We would like the logo diagonally across the card with the information split above and below the logo similar to sketch. happy to look at similar alternatives
Please use same colours as in logo design

Industry/Entity Type

Business

Contact Information for Business Card

Dwight Halloran
mob - 0491 738 204
ph - 02 6148 3920
fax - 02 6148 3975
email - dwight@kestrelbeams.com.au
14 Larkmoor Road, Taminda NSW 2340

Colin Marchetti
mob - 0438 912 557
ph - 02 6148 3920
fax - 02 6148 3975
email - colin@kestrelbeams.com.au

```html
<!DOCTYPE html>
<html lang="en">
<head>
<meta charset="UTF-8">
<title>Kestrel Beams – Business Cards</title>
<link href="https://fonts.googleapis.com/css2?family=Open+Sans:wght@400;600;700&display=swap" rel="stylesheet">
<style>
  :root {
    --ink: #1a1a1a;
    --text: #2b2b2b;
    --teal: #0e7b74;
    --paper: #ffffff;
    --backdrop: #e9e7e3;
    --edge: #b9b6b1;
  }
  * { margin: 0; padding: 0; box-sizing: border-box; }
  html, body {
    width: 1145px; height: 1200px; overflow: hidden;
    background: var(--backdrop);
    font-family: "Open Sans", sans-serif;
    color: var(--text);
  }
  .canvas { position: relative; width: 1145px; height: 1200px; }
  .card {
    position: absolute;
    background: var(--paper);
    border: 1px solid var(--edge);
  }
  .card--front { left: 169px; top: 22px; width: 943px; height: 538px; }
  .card--back  { left: 39px;  top: 591px; width: 944px; height: 540px; }

  .brand {
    position: absolute; left: 0; right: 0;
    display: flex; align-items: center; justify-content: center; gap: 22px;
  }
  .brand__square { width: 58px; height: 58px; background: var(--teal); }
  .brand__name {
    font-weight: 700; font-size: 76px; letter-spacing: 1px;
    color: var(--ink); line-height: 1;
  }
  .card--front .brand { top: 92px; }
  .card--back .brand { top: 212px; }

  .name-band { position: absolute; left: 0; right: 0; top: 277px; }
  .name-band__rule { height: 4px; background: var(--ink); }
  .name-band__bar {
    margin: 6px 0;
    height: 53px; background: var(--teal);
    display: flex; align-items: center; justify-content: center;
    color: #fff; font-weight: 700; font-size: 29px;
  }

  .contact {
    position: absolute; top: 389px; left: 0; right: 0;
    display: flex; justify-content: center;
    font-size: 23px; line-height: 39px;
  }
  .contact__col--left { text-align: right; padding-right: 17px; }
  .contact__col--right { padding-left: 17px; border-left: 2px solid var(--ink); }
  .contact__row { display: flex; align-items: center; gap: 8px; white-space: nowrap; }
  .contact__col--left .contact__row { justify-content: flex-end; }
  .contact__row--email { font-size: 20px; }
  .icon { width: 20px; height: 20px; fill: var(--text); flex: none; }

  .web {
    position: absolute; left: 0; right: 0; top: 423px;
    text-align: center; font-size: 29px; letter-spacing: 3px; color: var(--text);
  }
  .web__domain { font-weight: 600; }
</style>
</head>
<body>
<div class="canvas">

  <section class="card card--front">
    <div class="brand">
      <span class="brand__square"></span>
      <span class="brand__name">Kestrel Beams</span>
    </div>

    <div class="name-band">
      <div class="name-band__rule"></div>
      <div class="name-band__bar">Colin Marchetti</div>
      <div class="name-band__rule"></div>
    </div>

    <div class="contact">
      <div class="contact__col contact__col--left">
        <div class="contact__row">
          <svg class="icon" viewBox="0 0 20 20"><path d="M5 2l3 4-2 2c1 2 3 4 5 5l2-2 4 3-2 3c-6 0-12-6-12-13z"/></svg>
          02 6148 3920
        </div>
        <div class="contact__row">14 Larkmoor Road</div>
        <div class="contact__row">Corrawong NSW 2381</div>
      </div>
      <div class="contact__col contact__col--right">
        <div class="contact__row">
          <svg class="icon" viewBox="0 0 20 20"><path d="M6 1h8v18H6zM7.5 3v6h5V3zM7.5 11h1.5v1.5H7.5zm2.5 0h1.5v1.5H10zm-2.5 2.5h1.5V15H7.5zm2.5 0h1.5V15H10z"/></svg>
          0438 912 557
        </div>
        <div class="contact__row">
          <svg class="icon" viewBox="0 0 20 20"><path d="M5 3h9v5H5zM2 9h16v8H2zM6 11v2h8v-2z"/></svg>
          02 6148 3975
        </div>
        <div class="contact__row contact__row--email">
          <svg class="icon" viewBox="0 0 20 20"><path d="M2 5h16v11H2zm1.5 1.5L10 11l6.5-4.5z"/></svg>
          colin@kestrelbeams.com.au
        </div>
      </div>
    </div>
  </section>

  <section class="card card--back">
    <div class="brand">
      <span class="brand__square"></span>
      <span class="brand__name">Kestrel Beams</span>
    </div>
    <p class="web">www.<span class="web__domain">kestrelbeams</span>.com.au</p>
  </section>

</div>
</body>
</html>
```